New business card/stationary for a consulting company

I am looking for a clean and very professional looking business card for my consulting company as well as corresponding stationary. I am uploading our logo. I like simple and powerful for the feel. No graphics but I am open on everything else. Below is my contact information but would like the final to be in a version I can add my employees information into and print. Thank you.

Daniel Whitcombe
dan@ferncliffadvisory.com
2870 North 9th Avenue, Summit Floor, Elm Ridge, Illinois 60531
www.ferncliffadvisory.com

Industry/Entity Type

Consulting

Contact Information for Business Card

Daniel Whitcombe
dan@ferncliffadvisory.com
www.ferncliffadvisory.com

Font styles to use
Serif
Sans Serif

Requirements
Must have
• Our logo and the business card details.
Nice to have
• our website www.ferncliffadvisory.com

```html
<!DOCTYPE html>
<html lang="en">
<head>
<meta charset="utf-8">
<title>Ferncliff Advisory — Business Card</title>
<link rel="stylesheet" href="https://fonts.googleapis.com/css2?family=Questrial&family=Montserrat:wght@700&family=Roboto:wght@400;700&display=swap">
<style>
  :root {
    --navy: #03035f;
    --paper: #ffffff;
    --ink-grey: #4a4a4a;
    --silver: #e6e6ea;
    --backdrop: #ecebe8;
  }
  * { margin: 0; padding: 0; box-sizing: border-box; }
  html, body { width: 1200px; height: 960px; overflow: hidden; }
  body { position: relative; background: var(--backdrop); }

  .card { position: absolute; width: 600px; height: 342px; }
  .card-front { left: 302px; top: 129px; background: var(--paper); }
  .card-back { left: 299px; top: 488px; background: var(--navy); }

  .brand-mark { position: absolute; width: 38px; height: 38px; background: var(--navy); }
  .card-front .brand-mark { left: 395px; top: 46px; }
  .brand-name {
    position: absolute; font-family: "Questrial", sans-serif; letter-spacing: 1px;
    white-space: nowrap; color: var(--navy);
  }
  .card-front .brand-name { right: 44px; top: 98px; font-size: 22px; }

  .card-back .brand-mark { left: 273px; top: 122px; width: 54px; height: 54px; background: var(--silver); }
  .card-back .brand-name { left: 0; right: 0; text-align: center; top: 196px; font-size: 33px; color: var(--silver); }

  .accent-bar { position: absolute; left: 0; top: 210px; width: 8px; height: 98px; background: var(--navy); }
  .accent-rule { position: absolute; left: 11px; top: 210px; width: 2px; height: 98px; background: var(--navy); }

  .contact { position: absolute; left: 36px; top: 206px; font-family: "Roboto", sans-serif; color: var(--ink-grey); }
  .contact-name {
    font-family: "Montserrat", sans-serif; font-weight: 700; font-size: 19px;
    letter-spacing: 0.6px; color: var(--navy); line-height: 22px;
  }
  .contact-email { font-size: 14px; line-height: 18px; }
  .contact-address { font-size: 14px; line-height: 18px; margin-top: 9px; }
  .contact-web { font-size: 14px; font-weight: 700; line-height: 18px; margin-top: 2px; }
</style>
</head>
<body>
  <section class="card card-front">
    <div class="brand-mark"></div>
    <div class="brand-name">FERNCLIFF ADVISORY</div>

    <div class="accent-bar"></div>
    <div class="accent-rule"></div>
    <div class="contact">
      <div class="contact-name">DANIEL WHITCOMBE</div>
      <div class="contact-email">dan@ferncliffadvisory.com</div>
      <div class="contact-address">2870 North 9th Avenue<br>Summit Floor, Elm Ridge, Illinois 60531</div>
      <div class="contact-web">FERNCLIFFADVISORY.COM</div>
    </div>
  </section>

  <section class="card card-back">
    <div class="brand-mark"></div>
    <div class="brand-name">FERNCLIFF ADVISORY</div>
  </section>
</body>
</html>
```